BUSINESS CARD - HALLORAN FIELD SERVICES

I would like to create a business card for my fertilizer spreading business. I would like to incorporate my existing logo and also a description of the services offered. The business card will be given to farmers so must be kept simple but effective. It will also be left in stores so much also be eye catching in order to stand out from other cards.

Target Market(s)

FARMERS

Requirements
Must have
• FRONT OF CARD = EXISTING LOGO + "CUSTOMISED SPREADING" below the logo

REAR Of CARD = SERVICES OFFERED AND CONTACT DETAILS

- Bulk fertilizer including Lime, Gypsum, Manure & Compost
- Granular fertilizer including Single Super, Urea, Gran-am, & Custom Blends
- Modern equipment - Autosteer & Variable Rate Capable
- Friendly & Reliable Service
- Contact Gus: 0417 552 308
Nice to have
• utilize same color scheme as existing logo

```html
<!DOCTYPE html>
<html lang="en">
<head>
<meta charset="utf-8">
<title>Halloran Field Services – Business Card</title>
<link href="https://fonts.googleapis.com/css2?family=Figtree:wght@400;500;700;800&display=swap" rel="stylesheet">
<style>
  :root {
    --bg: #ece9e6;
    --card-white: #ffffff;
    --grey-top: #737373;
    --grey-bottom: #565656;
    --ink: #5a5a5a;
    --ink-soft: #5f5f5f;
    --orange: #f7941d;
    --shadow: 0 18px 34px rgba(0,0,0,0.28);
  }
  * { box-sizing: border-box; margin: 0; padding: 0; }
  html, body { width: 1200px; height: 1200px; overflow: hidden; }
  body {
    background: var(--bg);
    font-family: "Figtree", sans-serif;
    position: relative;
  }
  .card {
    position: absolute;
    left: 150px;
    width: 900px;
    height: 514px;
    border-radius: 32px;
    overflow: hidden;
    box-shadow: var(--shadow);
    background: var(--card-white);
  }
  .card--front { top: 50px; }
  .card--back { top: 636px; }

  .front-art { position: absolute; inset: 0; }

  .front-info {
    position: absolute;
    left: 38px;
    top: 124px;
    width: 290px;
    color: #fff;
  }
  .wordmark {
    font-weight: 800;
    font-size: 34px;
    letter-spacing: -0.5px;
    line-height: 1.08;
    color: #fff;
  }
  .holder-name {
    margin-top: 46px;
    color: var(--orange);
    font-weight: 800;
    font-size: 29px;
    letter-spacing: 0.3px;
  }
  .holder-role {
    font-size: 19px;
    font-weight: 500;
    margin-top: 4px;
  }
  .contact-list { list-style: none; margin-top: 18px; }
  .contact-list li {
    display: flex;
    align-items: center;
    gap: 10px;
    font-size: 19px;
    line-height: 25px;
  }
  .contact-list svg { width: 16px; height: 16px; flex: none; }

  .back-content {
    position: absolute;
    inset: 0;
    display: flex;
    flex-direction: column;
    align-items: center;
    text-align: center;
    padding-top: 96px;
  }
  .brand-dot {
    width: 132px;
    height: 132px;
    border-radius: 50%;
    background: var(--ink);
  }
  .back-wordmark {
    margin-top: 16px;
    font-weight: 800;
    font-size: 40px;
    letter-spacing: -0.6px;
    color: var(--ink);
    line-height: 1;
  }
  .tagline {
    margin-top: 10px;
    font-size: 23px;
    letter-spacing: 3px;
    color: var(--ink);
    font-weight: 400;
  }
  .services {
    list-style: none;
    margin-top: 34px;
    font-size: 19px;
    line-height: 25px;
    color: var(--ink-soft);
  }
</style>
</head>
<body>

<section class="card card--front" aria-label="Business card front">
  <svg class="front-art" viewBox="0 0 900 514" preserveAspectRatio="none" aria-hidden="true">
    <defs>
      <linearGradient id="greyFade" x1="0" y1="0" x2="0" y2="1">
        <stop offset="0" stop-color="#737373"/>
        <stop offset="1" stop-color="#565656"/>
      </linearGradient>
    </defs>
    <rect width="900" height="514" fill="url(#greyFade)"/>
    <rect x="567" y="0" width="333" height="514" fill="#fff"/>
    <circle cx="567" cy="272" r="242" fill="#fff"/>
    <circle cx="567" cy="272" r="228" fill="none" stroke="#606060" stroke-width="16"/>
  </svg>

  <div class="front-info">
    <div class="wordmark">Halloran Field<br>Services</div>
    <div class="holder-name">GUS HALLORAN</div>
    <div class="holder-role">President</div>
    <ul class="contact-list">
      <li>
        <svg viewBox="0 0 16 16"><path fill="#f7941d" d="M3.6 1.2l2.3 2.6-1.2 1.8c.9 2 2.4 3.6 4.6 4.7l1.8-1.2 2.6 2.3-1.4 2.3C7.3 13.3 2.7 8.7 1.3 3z"/></svg>
        0417 552 308
      </li>
      <li>
        <svg viewBox="0 0 16 16"><rect x="1.5" y="3.5" width="13" height="9" rx="1" fill="#f7941d"/><path d="M2 4.5l6 4.2 6-4.2" fill="none" stroke="#5f5f5f" stroke-width="1"/></svg>
        info@halloranfield.com
      </li>
      <li>
        <svg viewBox="0 0 16 16"><circle cx="8" cy="8" r="6.8" fill="#f7941d"/><path d="M4.5 5.5c1.5.2 2 1.3 1.6 2.5l1.6 1.3-.6 2.6M9.5 2.2c-.3 1.4.8 2 2 2.2" fill="none" stroke="#5f5f5f" stroke-width="1.1"/></svg>
        www.halloranfield.com
      </li>
    </ul>
  </div>
</section>

<section class="card card--back" aria-label="Business card back">
  <div class="back-content">
    <div class="brand-dot" aria-hidden="true"></div>
    <div class="back-wordmark">Halloran Field Services</div>
    <div class="tagline">CUSTOMISED SPREADING</div>
    <ul class="services">
      <li>Bulk fertilizer including Lime, Gypsum, Manure &amp; Compost</li>
      <li>Granular fertilizer including Single Super, Urea, Gran-am, &amp; Custom Blends</li>
      <li>Modern equipment - Autosteer &amp; Variable Rate Capable</li>
      <li>Friendly &amp; Reliable Service</li>
    </ul>
  </div>
</section>

</body>
</html>
```